Brimlow Plumbing Solutions

This is for my new plumbing company, I have attached an example of what I’m going for but want it to look better.

Target Market(s)

Home owners, real estate, etc.

Industry/Entity Type

Plumbing

Font styles to use
Other font styles liked:
• As per my logo and other examples uploaded

Colors

Designer to choose colors to be used in the design.

Requirements
Must have
• Must include my logo provided and similar to my flyer I have attached but better

```html
<!DOCTYPE html>
<html lang="en">
<head>
<meta charset="utf-8">
<title>Brimlow Plumbing Solutions – Flyer</title>
<link rel="stylesheet" href="https://fonts.googleapis.com/css2?family=Oswald:wght@400;500;600;700&family=Open+Sans:wght@300;400;700&display=swap">
<style>
  :root{
    --royal:#1a4fc4;
    --royal-deep:#0f3aa8;
    --navy:#0b2f8e;
    --tile:#0d3fae;
    --tile-edge:#5b8fe8;
    --gold:#f5c400;
    --cream:#fff6d6;
    --red:#e01b1b;
    --white:#ffffff;
    --page:#e6e6e6;
  }
  *{margin:0;padding:0;box-sizing:border-box}
  html,body{width:1200px;height:598px;overflow:hidden;background:var(--page)}
  .flyer{position:absolute;left:400px;top:17px;width:400px;height:564px;overflow:hidden;
    background:linear-gradient(180deg,var(--royal) 0%,var(--royal-deep) 100%);
    box-shadow:0 6px 14px rgba(0,0,0,.25);font-family:"Oswald",sans-serif;color:var(--white)}
  .abs{position:absolute}
  .side-band{left:0;top:116px;width:167px;height:406px;
    background:linear-gradient(180deg,#2a68d8 0%,#1d55c8 55%,#1848b8 100%)}
  .header-shape{left:0;top:0;width:400px;height:130px}
  .brand{left:52px;top:50px;color:var(--royal)}
  .brand-name{font-weight:700;font-size:34px;line-height:34px;letter-spacing:1px}
  .brand-tag{font-weight:700;font-size:10.5px;letter-spacing:.6px;margin-top:1px;padding-left:20px}
  .brand-dot{display:inline-block;width:14px;height:14px;border-radius:50%;background:var(--royal);margin-right:6px;vertical-align:2px}
  .badge{left:265px;top:32px;width:104px;height:104px}
  .badge-text{left:265px;top:49px;width:104px;text-align:center;font-weight:600;line-height:1}
  .badge-text .small{font-size:9.5px;line-height:11px}
  .badge-text .big{font-size:31px;font-weight:700;line-height:31px}
  .badge-text .disc{font-size:12px}
  .hand-icon{left:0;top:153px;width:49px;height:62px;
    background:linear-gradient(135deg,#3aa0e8 0%,#8fbf5a 55%,var(--gold) 100%);
    clip-path:polygon(0 0,80% 0,100% 25%,75% 100%,0 85%)}
  .tagline{left:50px;top:148px;width:110px;text-align:right;font-family:"Open Sans",sans-serif;font-weight:300;font-size:12px;line-height:13px;white-space:nowrap}
  .tagline b{font-family:"Oswald",sans-serif;font-weight:600;font-size:13px;line-height:13px}
  .headline{left:175px;top:146px;font-weight:600;font-size:24px;line-height:24px;text-transform:uppercase}
  .headline li{list-style:none;display:flex;align-items:center;white-space:nowrap}
  .headline li::before{content:"";width:0;height:0;border-top:5px solid transparent;border-bottom:5px solid transparent;border-left:7px solid var(--gold);margin-right:6px}
  .services-title{left:188px;top:223px;font-weight:600;font-size:16px;line-height:20px;letter-spacing:.3px}
  .photo{left:15px;width:119px;height:126px;border:2px solid var(--gold);border-radius:8px;
    background:linear-gradient(135deg,#4a4f58 0%,#23262c 60%,#6b6a66 100%)}
  .photo.one{top:250px}
  .photo.two{top:383px;background:linear-gradient(135deg,#7a7a78 0%,#3b3e44 55%,#a9a9a5 100%)}
  .tiles{left:148px;top:254px;width:234px;display:grid;grid-template-columns:repeat(3,72px);grid-auto-rows:81px;gap:7px 9px}
  .tile{background:var(--tile);border:1.5px solid var(--tile-edge);border-radius:7px;display:flex;flex-direction:column;align-items:center;padding-top:10px}
  .tile svg{width:28px;height:28px}
  .tile span{margin-top:6px;font-weight:500;font-size:10.5px;line-height:13px;text-align:center;text-transform:uppercase;white-space:nowrap}
  .contact-band{left:0;top:522px;width:400px;height:28px;
    background:linear-gradient(90deg,var(--cream) 0%,#fff 45%,var(--cream) 100%);
    border-top:1.5px solid var(--gold)}
  .phone{left:16px;top:524px;color:var(--navy);font-weight:700;font-size:17px;line-height:24px;display:flex;align-items:center;gap:5px}
  .phone svg{width:15px;height:15px}
  .mail{left:168px;top:526px;color:var(--navy);font-weight:500;font-size:7.5px;line-height:10px;text-transform:uppercase}
  .mail div{display:flex;align-items:center;gap:4px}
  .mail i{display:inline-block;width:7px;height:6px;background:var(--navy)}
  .social{left:345px;top:529px;display:flex;gap:5px}
  .social i{width:14px;height:14px;background:var(--royal);border-radius:2px;display:block}
</style>
</head>
<body>
<main class="flyer">
  <div class="abs side-band"></div>
  <svg class="abs header-shape" viewBox="0 0 400 130" aria-hidden="true">
    <path d="M400 8V26C370 45 340 60 305 72C340 55 370 35 400 8Z" fill="#4f8ee6"/>
    <path d="M0 0H400V28C300 88 170 112 0 110Z" fill="#fff"/>
    <path d="M0 110C170 112 300 88 400 28V36C300 98 170 120 0 116Z" fill="#f5c400"/>
  </svg>

  <div class="abs brand">
    <div class="brand-name"><span class="brand-dot"></span>BRIMLOW</div>
    <div class="brand-tag">PLUMBING SOLUTIONS</div>
  </div>

  <svg class="abs badge" viewBox="0 0 104 104" aria-hidden="true">
    <g fill="#e01b1b" transform="translate(52 52)">
      <rect x="-38" y="-38" width="76" height="76"/>
      <rect x="-38" y="-38" width="76" height="76" transform="rotate(22.5)"/>
      <rect x="-38" y="-38" width="76" height="76" transform="rotate(45)"/>
      <rect x="-38" y="-38" width="76" height="76" transform="rotate(67.5)"/>
    </g>
  </svg>
  <div class="abs badge-text">
    <div class="small">MENTION THIS<br>FLYER TO RECEIVE</div>
    <div class="big">15%</div>
    <div class="disc">DISCOUNT</div>
  </div>

  <div class="abs hand-icon" role="img" aria-label="Emblem of a hand holding a wrench"></div>
  <p class="abs tagline">Your local<br>reliable Sydney<br><b>PLUMBER</b><br><b>SPECIALISING</b><br>in all aspects of</p>

  <ul class="abs headline">
    <li>Plumbing</li>
    <li>Drainage</li>
    <li>Gas Maintenance</li>
  </ul>
  <div class="abs services-title">OUR SERVICE :</div>

  <div class="abs photo one" role="img" aria-label="Photo of a plumber tightening a brass valve with a wrench"></div>
  <div class="abs photo two" role="img" aria-label="Photo of hands fitting a copper pipe under a house"></div>

  <section class="abs tiles">
    <div class="tile">
      <svg viewBox="0 0 28 28" fill="none" stroke="#fff" stroke-width="2"><path d="M6 4l4 1 1 5-3 2c1 3 4 6 7 7l2-3 5 1 1 4c-1 2-3 3-5 3C10 23 4 17 3 9c0-2 1-4 3-5z"/><circle cx="19" cy="9" r="6"/><text x="19" y="12" font-size="7" fill="#fff" stroke="none" text-anchor="middle" font-family="Oswald">24</text></svg>
      <span>Emergency<br>Plumbing</span>
    </div>
    <div class="tile">
      <svg viewBox="0 0 28 28" fill="none" stroke="#fff" stroke-width="2.4"><circle cx="14" cy="14" r="7"/><path d="M14 2v4M14 22v4M2 14h4M22 14h4M5.5 5.5l3 3M19.5 19.5l3 3M5.5 22.5l3-3M19.5 8.5l3-3"/><path d="M11 17l6-6" stroke-width="2"/></svg>
      <span>Plumbing<br>Maintenance</span>
    </div>
    <div class="tile">
      <svg viewBox="0 0 28 28" fill="#fff"><rect x="6" y="2" width="3" height="10"/><rect x="2" y="12" width="12" height="3" rx="1"/><path d="M3 16h10c0 5-2 8-5 8s-5-3-5-8z"/><path d="M16 8h8v3h-5v4h-3z"/></svg>
      <span>Drainage<br>Maintanance</span>
    </div>
    <div class="tile">
      <svg viewBox="0 0 28 28" fill="#fff"><path d="M14 2c2 6 8 9 8 16a8 8 0 0 1-16 0c0-4 2-6 4-8 0 3 1 4 2 5 0-5 1-9 2-13z"/></svg>
      <span>Gas<br>Maintanance</span>
    </div>
    <div class="tile">
      <svg viewBox="0 0 28 28" fill="#fff"><rect x="6" y="8" width="12" height="17" rx="2"/><rect x="19" y="12" width="5" height="2"/><rect x="19" y="18" width="5" height="2"/><path d="M9 2v4M12 2v4M15 2v4" stroke="#fff" stroke-width="1.4"/></svg>
      <span>Hot Water<br>Systems</span>
    </div>
    <div class="tile">
      <svg viewBox="0 0 28 28" fill="none" stroke="#fff" stroke-width="2.2"><circle cx="12" cy="14" r="5"/><path d="M12 6v3M12 19v3M4 14h3M17 14h7M14 4h6M17 4v6"/><path d="M22 19c1 2 2 3 2 4a2 2 0 0 1-4 0c0-1 1-2 2-4z" fill="#fff"/></svg>
      <span>Leaking<br>Fixtures</span>
    </div>
    <div class="tile">
      <svg viewBox="0 0 28 28" fill="#fff"><rect x="5" y="3" width="9" height="5"/><rect x="11" y="6" width="5" height="14"/><rect x="11" y="17" width="13" height="5" rx="2"/><rect x="22" y="14" width="4" height="10"/></svg>
      <span>Blocked Sewer<br>&amp; Stormwater</span>
    </div>
    <div class="tile">
      <svg viewBox="0 0 28 28" fill="none" stroke="#fff" stroke-width="2"><rect x="3" y="15" width="22" height="8" rx="2"/><path d="M8 5c4-3 8-3 12 0M10 9c3-2 5-2 8 0"/><path d="M14 12v3"/></svg>
      <span>Camera &amp;<br>Locating</span>
    </div>
    <div class="tile">
      <svg viewBox="0 0 28 28" fill="none" stroke="#fff" stroke-width="2"><path d="M16 4a3 3 0 0 1 6 0v13a5 5 0 1 1-6 0z"/><circle cx="19" cy="21" r="2" fill="#fff"/><path d="M7 6v16M4 9l3-3 3 3M4 19l3 3 3-3"/></svg>
      <span>TMV<br>Maintanance</span>
    </div>
  </section>

  <div class="abs contact-band"></div>
  <div class="abs phone">
    <svg viewBox="0 0 16 16"><circle cx="8" cy="8" r="7.5" fill="#0b2f8e"/><path d="M5 4l2 .5.4 2-1.2.9c.5 1.2 1.4 2.1 2.6 2.6l.9-1.2 2 .4L12 11c-.5.8-1.4 1.2-2.3 1C7 11.3 4.7 9 4 6.3 3.8 5.4 4.2 4.5 5 4z" fill="#fff"/></svg>
    0400 555 019
  </div>
  <div class="abs mail">
    <div><i></i>brimlowplumbing@example.com</div>
    <div><i></i>@brimlowplumbing</div>
  </div>
  <div class="abs social"><i></i><i></i></div>
</main>
</body>
</html>
```